Verodex business card

Business card for sustainable investment company called "Verodex". Verodex is an exchange platform selling carbon credits between buyers and sellers. Carbon Credits are an environmental commodity for reducing global carbon emissions.

the card should obviously have our logo and the theme should be sustainability/environment mixed with a trading platform.

Contact Information for Business Card

Logo, Name, Title, Phone, Email

Colors
0054AA
0677BA
7BADD7
CADEEF
E8F1F8
0094D4
00A9DD
6FCCEA
C7EBF8
E9F6FB
00AB8E
00BBA5
67D7C9
C6EFE9
E9F9F6
59FF00
82FF00
B8FF75
E3FFCB
F4FFEA

```html
<!DOCTYPE html>
<html lang="en">
<head>
<meta charset="utf-8">
<title>Verodex Business Card</title>
<link rel="stylesheet" href="https://fonts.googleapis.com/css2?family=Montserrat:wght@600;700&family=Roboto:wght@400&display=swap">
<style>
  :root {
    --page-bg: #d6d6d6;
    --card-white: #ffffff;
    --ink-navy: #1b2942;
    --ink-text: #1f2430;
    --rule: #2a3346;
    --eco-green: #00bba5;
    --eco-teal: #00ab8e;
    --cyan: #2fe0e4;
    --sky: #00a9dd;
    --blue: #1f7fea;
    --icon-start: #00bba5;
    --icon-end: #0677ba;
    --shadow: rgba(0, 0, 0, 0.28);
  }
  * { box-sizing: border-box; margin: 0; padding: 0; }
  html, body {
    width: 1200px;
    height: 800px;
    overflow: hidden;
    background: var(--page-bg);
  }
  .sheet {
    position: relative;
    width: 1200px;
    height: 800px;
  }
  .card {
    position: absolute;
    top: 246px;
    width: 540px;
    height: 308px;
    box-shadow: 0 18px 40px var(--shadow);
  }
  /* Front */
  .card-front {
    left: 40px;
    background: var(--card-white);
    border-bottom: 3px solid var(--eco-green);
    text-align: center;
    color: var(--ink-text);
  }
  .brand-block {
    position: absolute;
    top: 26px;
    left: 0;
    right: 0;
    display: flex;
    flex-direction: column;
    align-items: center;
  }
  .brand-square {
    width: 34px;
    height: 34px;
    background: var(--eco-green);
    align-self: flex-start;
    margin-left: 148px;
    margin-bottom: 6px;
  }
  .brand-name {
    font-family: "Montserrat", sans-serif;
    font-weight: 700;
    font-size: 46px;
    line-height: 1;
    letter-spacing: 2px;
    color: var(--ink-navy);
  }
  .person {
    position: absolute;
    top: 130px;
    left: 0;
    right: 0;
  }
  .person-name {
    font-family: "Montserrat", sans-serif;
    font-weight: 700;
    font-size: 21px;
    letter-spacing: 0.5px;
    color: var(--ink-navy);
  }
  .person-title {
    margin-top: 2px;
    font-family: "Roboto", sans-serif;
    font-size: 14px;
    color: var(--ink-text);
  }
  .contact-rule {
    position: absolute;
    top: 201px;
    left: 70px;
    width: 400px;
    height: 34px;
  }
  .contact-line {
    position: absolute;
    top: 248px;
    left: 0;
    right: 0;
    font-family: "Roboto", sans-serif;
    font-size: 14.5px;
    color: var(--ink-text);
  }
  .contact-line .sep { padding: 0 6px; }
  /* Back */
  .card-back {
    left: 620px;
    background: linear-gradient(35deg, var(--cyan) 0%, var(--sky) 50%, var(--blue) 100%);
    display: flex;
    align-items: center;
    justify-content: center;
    gap: 22px;
  }
  .back-square {
    width: 46px;
    height: 46px;
    background: var(--card-white);
  }
  .back-brand {
    font-family: "Montserrat", sans-serif;
    font-weight: 700;
    font-size: 50px;
    line-height: 1;
    letter-spacing: 2px;
    color: var(--card-white);
  }
</style>
</head>
<body>
<main class="sheet">
  <section class="card card-front" aria-label="Business card front">
    <div class="brand-block">
      <div class="brand-square" aria-hidden="true"></div>
      <div class="brand-name">VERODEX</div>
    </div>
    <div class="person">
      <div class="person-name">DANIEL MORROW</div>
      <div class="person-title">Managing Director</div>
    </div>
    <svg class="contact-rule" viewBox="0 0 400 34" aria-hidden="true">
      <defs>
        <linearGradient id="iconFill" x1="0" y1="1" x2="1" y2="0">
          <stop offset="0" stop-color="var(--icon-start)"/>
          <stop offset="1" stop-color="var(--icon-end)"/>
        </linearGradient>
      </defs>
      <line x1="20" y1="17" x2="380" y2="17" stroke="var(--rule)" stroke-width="1"/>
      <g transform="translate(20 17)">
        <circle r="15" fill="url(#iconFill)"/>
        <rect x="-7" y="-5" width="14" height="10" fill="none" stroke="#fff" stroke-width="1.6"/>
        <polyline points="-7,-5 0,1 7,-5" fill="none" stroke="#fff" stroke-width="1.6"/>
      </g>
      <g transform="translate(200 17)">
        <circle r="15" fill="url(#iconFill)"/>
        <path d="M-6 -6 q-2 8 5 12 l2 -2 q1-1 2 0 l2 2 q1 1 0 2 q-3 2 -7 -1 q-6 -5 -6 -10 q0 -3 2 -4 q1 -1 2 0 l2 2 q1 1 0 2 z" fill="#fff"/>
      </g>
      <g transform="translate(380 17)">
        <circle r="15" fill="url(#iconFill)"/>
        <circle r="7" fill="none" stroke="#fff" stroke-width="1.4"/>
        <ellipse rx="3" ry="7" fill="none" stroke="#fff" stroke-width="1.2"/>
        <line x1="-7" y1="0" x2="7" y2="0" stroke="#fff" stroke-width="1.2"/>
      </g>
    </svg>
    <div class="contact-line">
      contact@verodex.net<span class="sep">|</span>031-555 210 448<span class="sep">|</span>www.verodex.net
    </div>
  </section>

  <section class="card card-back" aria-label="Business card back">
    <div class="back-square" aria-hidden="true"></div>
    <div class="back-brand">VERODEX</div>
  </section>
</main>
</body>
</html>
```